Accounting firm needing business card / letterhead designed
Marcus L. Trenholm, CPA
marcus@veltrowledger.com
www.veltrowledger.com
842 E Alder Ave Perrysburg, OH 43827
419-562-0974

```html
<!DOCTYPE html>
<html lang="en">
<head>
<meta charset="utf-8">
<title>Veltrow Ledger — Business Card</title>
<link rel="stylesheet" href="https://fonts.googleapis.com/css2?family=Roboto:wght@400;500;700&family=Roboto+Condensed:wght@700&display=swap">
<style>
  :root {
    --navy: #262262;
    --green: #8dc63f;
    --paper: #f3f3f3;
    --stage: #dcdcdc;
    --ink-grey: #555555;
    --white: #ffffff;
  }
  * { margin: 0; padding: 0; box-sizing: border-box; }
  html, body { width: 1200px; height: 960px; overflow: hidden; }
  body {
    position: relative;
    background: var(--stage);
    font-family: "Roboto", Arial, sans-serif;
  }
  .card {
    position: absolute;
    width: 600px;
    height: 342px;
    border-radius: 18px;
    overflow: hidden;
  }
  /* Front */
  .card--front {
    left: 320px;
    top: 108px;
    background: var(--navy);
  }
  .front-name {
    position: absolute;
    left: 0; right: 0;
    top: 122px;
    text-align: center;
    color: var(--white);
    font-weight: 700;
    font-size: 58px;
    letter-spacing: 1px;
    text-transform: uppercase;
  }
  .front-web {
    position: absolute;
    left: 0; right: 0;
    top: 280px;
    text-align: center;
    color: var(--white);
    font-size: 14px;
    letter-spacing: 6px;
  }
  /* Back */
  .card--back {
    left: 320px;
    top: 493px;
    background: var(--paper);
  }
  .holder-name {
    position: absolute;
    left: 26px;
    top: 20px;
    font-family: "Roboto Condensed", "Arial Narrow", sans-serif;
    font-weight: 700;
    font-size: 21px;
    color: var(--navy);
  }
  .back-name {
    position: absolute;
    left: 20px;
    top: 145px;
    color: var(--navy);
    font-weight: 700;
    font-size: 40px;
    text-transform: uppercase;
    letter-spacing: 0.5px;
  }
  .contact-band {
    position: absolute;
    left: 345px;
    top: 138px;
    width: 255px;
    height: 67px;
    background: var(--green);
    clip-path: polygon(0 0, 100% 0, 100% 100%, 0 100%, 18px 50%);
  }
  .contact-list {
    position: absolute;
    right: 24px;
    top: 142px;
    list-style: none;
    color: var(--white);
    font-size: 14.5px;
    line-height: 19px;
    text-align: right;
  }
  .contact-list li {
    display: flex;
    align-items: center;
    justify-content: flex-end;
    gap: 7px;
  }
  .contact-list svg { width: 12px; height: 12px; flex: none; }
  .address {
    position: absolute;
    right: 22px;
    top: 298px;
    color: var(--ink-grey);
    font-size: 14.5px;
  }
</style>
</head>
<body>
  <section class="card card--front">
    <div class="front-name">Veltrow Ledger</div>
    <div class="front-web">www.veltrowledger.com</div>
  </section>

  <section class="card card--back">
    <div class="holder-name">Marcus L. Trenholm, CPA</div>
    <div class="back-name">Veltrow Ledger</div>
    <div class="contact-band"></div>
    <ul class="contact-list">
      <li>419-562-0974
        <svg viewBox="0 0 24 24" aria-hidden="true"><path fill="#262262" d="M6.6 10.8a15.2 15.2 0 0 0 6.6 6.6l2.2-2.2c.3-.3.7-.4 1-.2 1.1.4 2.3.6 3.6.6.6 0 1 .4 1 1V20c0 .6-.4 1-1 1A17 17 0 0 1 3 4c0-.6.4-1 1-1h3.5c.6 0 1 .4 1 1 0 1.3.2 2.5.6 3.6.1.3 0 .7-.2 1z"/></svg>
      </li>
      <li>marcus@veltrowledger.com
        <svg viewBox="0 0 24 24" aria-hidden="true"><rect x="2" y="5" width="20" height="14" fill="#262262"/><path d="M2 5l10 8 10-8" fill="none" stroke="#8dc63f" stroke-width="2"/></svg>
      </li>
      <li>www.veltrowledger.com
        <svg viewBox="0 0 24 24" aria-hidden="true"><circle cx="12" cy="12" r="10" fill="#262262"/><path d="M2 12h20M12 2c3 3 3 17 0 20M12 2c-3 3-3 17 0 20" fill="none" stroke="#8dc63f" stroke-width="1.5"/></svg>
      </li>
    </ul>
    <div class="address">842 E Alder Ave, Perrysburg, OH 43827</div>
  </section>
</body>
</html>
```